Computer consultant business card

Bexil Software is a newly started computer consulting company. It's a small one-man company that provides mostly Vornix applications but also websites in collaboration with designers. I'm running this company on the side of full time university studies.

I want the final design to be clean and memorable. Be creative! :)

Some inspiration:
http://www.pixelmarta.com/design/48317
http://www.pixelmarta.com/design/2739164/business-card-design-by-frostlynk
http://www.pixelmarta.com/design/604281/business-card-design-by-koralind-vestrabanu

See attachment for my company logo.
Updates

I would like to thank everyone for submitting! I'll need a couple of days to review and ultimately select a design.

Target Market(s)

Non-technical entrepreneurs and small companies.

Industry/Entity Type

University

Requirements
Must have
• My company logo.
In any way, both colors from my logo.
First- and last name, e-mail and phone number.
Double-sided design.
Nice to have
• Something creative with the symbol in my logo

```html
<!DOCTYPE html>
<html lang="en">
<head>
<meta charset="utf-8">
<title>Bexil Software – Business Card</title>
<link rel="stylesheet" href="https://fonts.googleapis.com/css2?family=Arimo:wght@400;700&display=swap">
<style>
  :root {
    --backdrop: #e6e6e8;
    --ink-dark: #2f2d2e;
    --brand-blue: #2a6fe8;
    --paper: #ffffff;
    --text-dark: #2f2d2e;
    --text-light: #ffffff;
    --text-muted: #d9d9db;
  }
  * { box-sizing: border-box; margin: 0; padding: 0; }
  html, body {
    width: 1200px; height: 938px; overflow: hidden;
    background: var(--backdrop);
    font-family: "Arimo", Arial, sans-serif;
  }
  .canvas { position: relative; width: 1200px; height: 938px; }
  .card {
    position: absolute; width: 700px; height: 400px;
    overflow: hidden;
    box-shadow: 0 6px 22px rgba(0,0,0,.18);
  }
  .card--front { left: 60px; top: 46px; background: var(--paper); }
  .card--back  { left: 440px; top: 492px; background: var(--ink-dark); }

  .front-band { position: absolute; inset: 0; }

  .holder {
    position: absolute; right: 44px; top: 30px;
    text-align: right; color: var(--text-light);
  }
  .holder__first { font-size: 26px; font-weight: 700; }
  .holder__last { font-size: 21px; font-weight: 400; color: var(--text-muted); margin-top: 4px; }

  .brand { position: absolute; display: flex; align-items: center; gap: 22px; }
  .brand__dot { border-radius: 50%; flex: none; }
  .brand__name { font-weight: 700; letter-spacing: 1px; line-height: 1; }

  .card--front .brand { left: 56px; top: 178px; }
  .card--front .brand__dot { width: 74px; height: 74px; background: var(--brand-blue); }
  .card--front .brand__name { font-size: 84px; color: var(--text-dark); }

  .contact {
    position: absolute; left: 56px; bottom: 34px;
    list-style: none; color: var(--text-dark); font-size: 19px;
  }
  .contact li { display: flex; align-items: center; gap: 10px; margin-top: 6px; }
  .contact svg { width: 16px; height: 16px; flex: none; }
  .contact .no-icon { padding-left: 26px; }

  .card--back .brand { left: 50%; top: 50%; transform: translate(-50%, -50%); gap: 34px; }
  .card--back .brand__dot { width: 120px; height: 120px; background: var(--text-light); }
  .card--back .brand__name { font-size: 118px; color: var(--text-light); }
</style>
</head>
<body>
<main class="canvas">

  <section class="card card--front" aria-label="Business card front">
    <svg class="front-band" viewBox="0 0 700 400" preserveAspectRatio="none" aria-hidden="true">
      <path d="M0 0 H700 V150 Q340 40 0 28 Z" fill="var(--ink-dark)"/>
      <path d="M0 28 Q340 40 700 150" fill="none" stroke="var(--brand-blue)" stroke-width="5"/>
    </svg>

    <div class="holder">
      <p class="holder__first">First Name</p>
      <p class="holder__last">Last Name</p>
    </div>

    <div class="brand">
      <span class="brand__dot"></span>
      <span class="brand__name">bexil</span>
    </div>

    <ul class="contact">
      <li>
        <svg viewBox="0 0 16 16" aria-hidden="true"><circle cx="8" cy="8" r="7.5" fill="var(--brand-blue)"/><path d="M5.5 4.5l1.5 1.5-1 1c.6 1.3 1.6 2.3 2.9 2.9l1-1 1.5 1.5-1.2 1.2c-2.9-.6-5.3-3-5.9-5.9z" fill="#fff"/></svg>
        555-208-4196
      </li>
      <li>
        <svg viewBox="0 0 16 16" aria-hidden="true"><circle cx="8" cy="8" r="7.5" fill="var(--brand-blue)"/><rect x="4" y="5" width="8" height="6" rx="1" fill="#fff"/><path d="M4.3 5.4L8 8.3l3.7-2.9" fill="none" stroke="var(--brand-blue)" stroke-width="1"/></svg>
        info@bexil-apps.net
      </li>
      <li class="no-icon">Street Name, City Name, State, City Zip Code</li>
    </ul>
  </section>

  <section class="card card--back" aria-label="Business card back">
    <div class="brand">
      <span class="brand__dot"></span>
      <span class="brand__name">bexil</span>
    </div>
  </section>

</main>
</body>
</html>
```